Premium Business Card for Wealth Creation

Please see attached business card for example.
Happy to look at options like Blue background with Yellow
Target Market(s)
People who want to buy investment property or create wealth
Industry/Entity Type
Investment
Contact Information for Business Card
Tel: 1800 314 579
Mobile: 0417 265 904
Address: Suite 4, 64 Carrow Lane Ferndale Qld 4812
Name: Martin Feldway
Title: CEO
Website: www.quolvane.com.au
Email: martin@quolvane.com.au
Font styles to use
Sans Serif
Colors
0255a3
fbed22
Requirements
Must have
- Look great

```html
<!DOCTYPE html>
<html lang="en">
<head>
<meta charset="utf-8">
<title>Quolvane Business Card</title>
<link href="https://fonts.googleapis.com/css2?family=Open+Sans:wght@400;600;700;800&display=swap" rel="stylesheet">
<style>
  :root {
    --blue-deep: #0255a3;
    --blue-mid: #1f5fbf;
    --blue-light: #4f82d2;
    --yellow: #fbed22;
    --yellow-deep: #e6c82a;
    --white: #ffffff;
    --paper: #f4f4f2;
    --bg: #e9e7e2;
    --ink-blue: #2a55b8;
    --web-ink: #5a4a10;
  }
  * { margin: 0; padding: 0; box-sizing: border-box; }
  html, body { width: 1200px; height: 780px; overflow: hidden; }
  body {
    background: var(--bg);
    font-family: "Open Sans", Arial, sans-serif;
    display: flex;
    align-items: center;
    justify-content: center;
    gap: 40px;
  }
  .card {
    position: relative;
    width: 540px;
    height: 310px;
    overflow: hidden;
    box-shadow: 0 6px 18px rgba(0,0,0,0.18);
  }

  /* Front */
  .card-front { background: var(--paper); }
  .front-brand {
    position: absolute;
    left: 0; top: 0; right: 0;
    height: 118px;
    display: flex;
    align-items: center;
    padding-left: 36px;
    gap: 14px;
  }
  .brand-dot {
    width: 46px; height: 46px;
    border-radius: 50%;
    background: var(--ink-blue);
  }
  .brand-name {
    font-weight: 800;
    font-size: 52px;
    letter-spacing: 1px;
    color: var(--ink-blue);
    line-height: 1;
  }
  .front-band {
    position: absolute;
    left: 0; right: 0; top: 118px;
    height: 146px;
    background: linear-gradient(100deg, var(--blue-mid) 0%, var(--blue-light) 45%, var(--blue-mid) 100%);
  }
  .front-strip {
    position: absolute;
    left: 0; right: 0; bottom: 0;
    height: 46px;
    background: linear-gradient(90deg, var(--yellow-deep), var(--yellow));
  }
  .person {
    position: absolute;
    left: 30px; bottom: 12px;
    color: var(--white);
  }
  .person-name { font-weight: 800; font-size: 20px; line-height: 1.1; }
  .person-title { color: var(--yellow); font-size: 14px; font-weight: 600; margin-bottom: 4px; }
  .contact-list { list-style: none; }
  .contact-item {
    display: flex; align-items: center; gap: 7px;
    font-size: 13px; line-height: 19px;
  }
  .contact-icon {
    width: 13px; height: 13px;
    background: var(--yellow);
    display: inline-flex; align-items: center; justify-content: center;
    flex: none;
  }
  .office {
    position: absolute;
    right: 22px; bottom: 12px;
    color: var(--white);
    font-size: 13px;
    line-height: 19px;
    display: flex;
    gap: 7px;
    align-items: flex-start;
  }
  .office .contact-icon { margin-top: 3px; }

  /* Back */
  .card-back {
    background: radial-gradient(ellipse at 50% 45%, #2566c8 0%, var(--blue-deep) 75%);
  }
  .back-name {
    position: absolute;
    left: 0; right: 0; top: 82px;
    text-align: center;
    font-weight: 800;
    font-size: 64px;
    letter-spacing: 2px;
    color: var(--white);
  }
  .back-strip {
    position: absolute;
    left: 0; right: 0; bottom: 0;
    height: 46px;
    background: linear-gradient(90deg, var(--yellow-deep), var(--yellow));
    display: flex; align-items: center; justify-content: center;
  }
  .back-web { color: var(--web-ink); font-size: 13px; letter-spacing: 0.3px; }
</style>
</head>
<body>

<section class="card card-front" aria-label="Business card front">
  <div class="front-brand">
    <span class="brand-dot"></span>
    <span class="brand-name">QUOLVANE</span>
  </div>
  <div class="front-band">
    <div class="person">
      <p class="person-name">Martin Feldway</p>
      <p class="person-title">CEO</p>
      <ul class="contact-list">
        <li class="contact-item">
          <span class="contact-icon"><svg width="9" height="9" viewBox="0 0 10 10"><path d="M2 1 L4 1 L4.6 3 L3.4 4 Q4.5 6 6 6.6 L7 5.4 L9 6 L9 8 Q5 9 2 5 Q1 3 2 1Z" fill="#0255a3"/></svg></span>
          1800 314 579
        </li>
        <li class="contact-item">
          <span class="contact-icon"><svg width="9" height="9" viewBox="0 0 10 10"><rect x="3" y="0.5" width="4" height="9" rx="0.8" fill="#0255a3"/><rect x="3.7" y="1.5" width="2.6" height="5.5" fill="#fbed22"/></svg></span>
          0417 265 904
        </li>
        <li class="contact-item">
          <span class="contact-icon"><svg width="9" height="9" viewBox="0 0 10 10"><rect x="1" y="2" width="8" height="6" fill="none" stroke="#0255a3" stroke-width="1.2"/><path d="M1 2 L5 5.5 L9 2" fill="none" stroke="#0255a3" stroke-width="1.2"/></svg></span>
          martin@quolvane.com.au
        </li>
      </ul>
    </div>
    <div class="office">
      <span class="contact-icon"><svg width="9" height="9" viewBox="0 0 10 10"><circle cx="5" cy="5" r="3.8" fill="none" stroke="#0255a3" stroke-width="1"/><path d="M1.2 5 H8.8 M5 1.2 V8.8" stroke="#0255a3" stroke-width="0.9"/></svg></span>
      <div>
        <p>www.quolvane.com.au</p>
        <p>Suite 4, 64 Carrow Lane</p>
        <p>Ferndale Qld 4812</p>
      </div>
    </div>
  </div>
  <div class="front-strip"></div>
</section>

<section class="card card-back" aria-label="Business card back">
  <p class="back-name">QUOLVANE</p>
  <div class="back-strip">
    <span class="back-web">www.quolvane.com.au</span>
  </div>
</section>

</body>
</html>
```